Boutique Real Estate Brokerage Tessly Realty Website Design

Winning designer work on migrate as well through nest ferry.
We need a new website as an informational hub to aid our print and digital strategy as well as showing that we are located in Brooklyn and Florida. I have a boutique real estate brokerage and advisory firm specializing in residential leasing, multifamily sales and 1031 Exchange appropriation. This won't be a portal to search properties, it will be a place for information. I'd like space for an ebook to be downloaded and information on my probate sales and multifamily leasing marketing campaigns. I included my logo and will leave it up to the designer to come up with colors to match it. I have also attached verbiage for each page. The final design should have a modern high end look that reflects gentrifying Brooklyn as well as beautiful Florida.
Thank you!
Target Market(s)
Owners of income producing real estate and develop-able land in Brooklyn, NY and Florida.
Industry/Entity Type
Real Estate
Coding
Coded - Design and coding required
Number of Pages Required
5+ page
Colors
Designer to choose colors to be used in the design.
Requirements
Must have
- A modern elegant look
Nice to have
- pictures of brooklyn and florida
Should not have
- real estate search pages

```html
<!DOCTYPE html>
<html lang="en">
<head>
<meta charset="utf-8">
<title>Tessly Realty NYC</title>
<link href="https://fonts.googleapis.com/css2?family=Barlow:wght@400;500;600;700&family=Dancing+Script:wght@500&display=swap" rel="stylesheet">
<style>
:root{
  --black:#050505;
  --ink:#222730;
  --text:#2f2f2f;
  --white:#ffffff;
  --footer:#f1f1f1;
  --footer-bar:#e3e3e3;
  --dark-band:#262626;
}
*{margin:0;padding:0;box-sizing:border-box}
html,body{width:1200px;height:2317px;overflow:hidden}
body{position:relative;font-family:"Barlow",sans-serif;color:var(--text);background:var(--white)}
a{text-decoration:none}
.abs{position:absolute}

/* header */
.site-header{left:0;top:0;width:1200px;height:103px;background:var(--black)}
.brand{left:74px;top:30px;display:flex;align-items:center;gap:12px;color:#d8d8d8;font-weight:700;font-size:15px;letter-spacing:2px;text-transform:uppercase}
.brand-mark{width:44px;height:44px;background:#7a7a7a}
.main-nav{right:70px;top:0;height:103px;display:flex;align-items:center;gap:35px}
.main-nav a{color:var(--white);font-weight:500;font-size:17px;position:relative;height:103px;display:flex;align-items:center}
.main-nav a.active::after{content:"";position:absolute;left:-9px;right:-9px;bottom:0;height:4px;background:var(--white)}
.main-nav a.btn-signup{background:linear-gradient(#6e6e6e,#4a4a4a);padding:0 25px;border-radius:8px;height:44px;margin-left:0}

/* hero */
.hero{left:0;top:103px;width:1200px;height:559px;background:linear-gradient(100deg,#6b7a3c 0%,#4a3428 22%,#8a3a22 45%,#5a2a1e 65%,#9a4a2a 82%,#3a3a2a 100%)}
.hero-title{left:0;top:300px;width:1200px;text-align:center;color:var(--white);font-weight:700;font-size:62px;letter-spacing:1px;line-height:74px}
.hero-tag{left:275px;top:375px;width:650px;height:46px;background:rgba(60,30,20,.55);color:var(--white);font-family:"Dancing Script",cursive;font-size:28px;text-align:center;line-height:46px}
.hero-arrows{left:556px;top:577px;display:flex;gap:10px}

/* section titles */
.section-title{font-weight:700;font-size:38px;color:var(--ink);text-align:center;letter-spacing:.5px;white-space:nowrap}
.wave{display:block;margin:6px auto 0}

.help-title{left:0;top:708px;width:1200px}
.card{top:803px;width:332px;height:207px;display:flex;flex-direction:column;align-items:center;justify-content:center;color:var(--white);text-align:center}
.card h3{font-weight:700;font-size:20px}
.card-leasing{left:74px;background:linear-gradient(135deg,#4b5456,#6b6a60 50%,#2c2a28)}
.card-sales{left:434px;background:var(--dark-band)}
.card-sales p{font-size:14px;line-height:22px;margin:12px 36px 14px;color:#e4e4e4}
.card-site{left:794px;background:linear-gradient(180deg,#3c4850 0%,#4c5448 45%,#3a3528 100%)}

/* welcome */
.welcome{left:84px;top:1108px;width:495px}
.welcome .section-title{font-size:35px;letter-spacing:0}
.welcome p{margin-top:22px;font-size:14px;line-height:22.4px;text-align:justify}
.btn{display:inline-block;background:linear-gradient(#5e5e5e,#3a3a3a);color:var(--white);font-weight:700;font-size:14px;border-radius:7px;text-align:center}
.welcome .btn{margin:31px 0 0 182px;width:132px;height:42px;line-height:42px}
.welcome-photo{left:599px;top:1081px;width:601px;height:414px;background:linear-gradient(180deg,#4f86c6 0%,#3a6fa8 18%,#6f7a6e 35%,#8b8676 65%,#c9c4b2 100%)}

/* ebook */
.ebook{left:0;top:1495px;width:1200px;height:497px;background:linear-gradient(180deg,#2d2d2d,#1f1f1f 60%,#2a2624)}
.ebook-inner{left:0;top:1577px;width:1200px;text-align:center;color:var(--white)}
.ebook-inner .section-title{color:var(--white)}
.ebook-inner h3{margin-top:22px;font-size:30px;line-height:36px;font-weight:700}
.ebook-inner p{margin:18px auto 0;width:620px;font-size:14.5px;line-height:22px;color:#e6e6e6}
.ebook-inner .btn{margin-top:34px;width:186px;height:40px;line-height:40px;font-size:13.5px}

/* footer */
.site-footer{left:0;top:1992px;width:1200px;height:273px;background:var(--footer)}
.footer-col{top:46px}
.footer-col h4{font-weight:700;font-size:27px;color:var(--black);margin-bottom:24px}
.footer-col p,.footer-col li{font-size:14px;line-height:28px;color:var(--text)}
.col-about{left:103px;width:290px}
.col-contact{left:473px;width:300px}
.col-links{left:843px}
.footer-col ul{list-style:none}
.footer-col li{display:flex;align-items:center;gap:14px}
.contact-row{display:flex;gap:20px}
.contact-row svg{flex:none;margin-top:6px}
.footer-brand{display:flex;align-items:center;gap:10px;margin-top:12px;font-weight:700;font-size:14px;letter-spacing:2px;text-transform:uppercase;color:#3a3a3a}
.footer-brand .mark{width:40px;height:40px;background:#6a6a6a}
.footer-bar{left:0;top:2265px;width:1200px;height:52px;background:var(--footer-bar)}
.copyright{left:74px;top:16px;font-size:13px;color:var(--black)}
.social{right:70px;top:19px;display:flex;gap:26px}
.social span{width:13px;height:13px;border-radius:50%;background:#1a1a1a}
</style>
</head>
<body>

<header class="site-header abs">
  <div class="brand abs"><span class="brand-mark"></span>Tessly Realty</div>
  <nav class="main-nav abs">
    <a class="active" href="#">HOME</a>
    <a href="#">ABOUT US</a>
    <a href="#">SERVICES</a>
    <a href="#">CONTACT</a>
    <a class="btn-signup" href="#">SIGN UP</a>
  </nav>
</header>

<section class="hero abs" role="img" aria-label="Photo of a Brooklyn brownstone street with red brick facades, stoops and trees"></section>
<h1 class="hero-title abs">TESSLY REALTY NYC</h1>
<div class="hero-tag abs">Assisting landlords increase profits While decreasing the stress.</div>
<div class="hero-arrows abs">
  <svg width="36" height="36" viewBox="0 0 36 36"><circle cx="18" cy="18" r="16" fill="none" stroke="#fff" stroke-width="2"/><path d="M24 18H12M17 13l-5 5 5 5" fill="none" stroke="#fff" stroke-width="2"/></svg>
  <svg width="36" height="36" viewBox="0 0 36 36"><circle cx="18" cy="18" r="16" fill="none" stroke="#fff" stroke-width="2"/><path d="M12 18h12M19 13l5 5-5 5" fill="none" stroke="#fff" stroke-width="2"/></svg>
</div>

<div class="help-title abs">
  <h2 class="section-title">HOW WE CAN HELP</h2>
  <svg class="wave" width="132" height="8" viewBox="0 0 132 8"><path d="M0 4q4.125-4 8.25 0t8.25 0 8.25 0 8.25 0 8.25 0 8.25 0 8.25 0 8.25 0 8.25 0 8.25 0 8.25 0 8.25 0 8.25 0 8.25 0 8.25 0 8.25 0" fill="none" stroke="#333" stroke-width="1.6"/></svg>
</div>

<div class="card card-leasing abs" role="img" aria-label="Photo of a modern apartment kitchen and dining area"><h3>MULTI-FAMILY LEASING</h3></div>
<div class="card card-sales abs">
  <h3>MULTI-FAMILY SALES</h3>
  <p>We specialize in sourcing quality tenants for landlords with high income, good credit and no evictions.</p>
  <svg width="36" height="36" viewBox="0 0 36 36"><circle cx="18" cy="18" r="16" fill="none" stroke="#fff" stroke-width="2"/><path d="M18 11v14M11 18h14" stroke="#fff" stroke-width="2"/></svg>
</div>
<div class="card card-site abs" role="img" aria-label="Aerial photo of land and water at dusk"><h3>SITE SELECTION ADVISORY</h3></div>

<section class="welcome abs">
  <h2 class="section-title">WELCOME TO TESSLY REALTY</h2>
  <svg class="wave" width="132" height="8" viewBox="0 0 132 8"><path d="M0 4q4.125-4 8.25 0t8.25 0 8.25 0 8.25 0 8.25 0 8.25 0 8.25 0 8.25 0 8.25 0 8.25 0 8.25 0 8.25 0 8.25 0 8.25 0 8.25 0 8.25 0" fill="none" stroke="#333" stroke-width="1.6"/></svg>
  <p>Tessly Realty NYC is a full service real estate brokerage firm located in Brooklyn, NY and West Palm Beach, FL. We specializes in assisting landlords by increasing their profits while decreasing their stress. Our firm concentrates on multifamily sales and leasing; distressed sales and 1031 Exchange property appropriation. With more than 12 years of experience in Brooklyn, we've narrowed our scope to its Northern and Eastern neighborhoods. Our West Palm Beach office specializes in Opportunity Zones in Palm Beach, Broward, Dade and Orange Counties.</p>
  <a class="btn" href="#">READ MORE</a>
</section>
<div class="welcome-photo abs" role="img" aria-label="Aerial photo of a Florida beachfront city with high-rise towers and ocean"></div>

<section class="ebook abs" role="img" aria-label="Dark photo of a bridge walkway with city skyline in the background"></section>
<div class="ebook-inner abs">
  <h2 class="section-title">DOWNLOAD EBOOK</h2>
  <svg class="wave" width="132" height="8" viewBox="0 0 132 8"><path d="M0 4q4.125-4 8.25 0t8.25 0 8.25 0 8.25 0 8.25 0 8.25 0 8.25 0 8.25 0 8.25 0 8.25 0 8.25 0 8.25 0 8.25 0 8.25 0 8.25 0 8.25 0" fill="none" stroke="#fff" stroke-width="1.6"/></svg>
  <h3>EBOOK FOR PROBATE SALES AND MULTIFAMILY<br>LEASING MARKETING CAMPAIGNS</h3>
  <p>Sed ut perspiciatis unde omnis iste natus error sit voluptatem accusantium doloremque laudantium, totam rem aperiam, eaque ipsa quae ab illo inventore veritatis et quasi</p>
  <a class="btn" href="#">DOWNLOAD BOOK</a>
</div>

<footer class="site-footer abs">
  <div class="footer-col col-about abs">
    <h4>ABOUT</h4>
    <p>Tessly Realty NYC specializes in assisting landlords by increasing their profits while decreasing their stress.</p>
    <div class="footer-brand"><span class="mark"></span>Tessly Realty</div>
  </div>
  <div class="footer-col col-contact abs">
    <h4>CONTACT INFO</h4>
    <div class="contact-row"><svg width="16" height="16" viewBox="0 0 16 16"><path d="M3 1l3 3-2 2c1 2 3 4 5 5l2-2 3 3-2 3C7 15 1 9 1 3z" fill="#222"/></svg><p>555-014-2290</p></div>
    <div class="contact-row"><svg width="16" height="16" viewBox="0 0 16 16"><rect x="1" y="3" width="14" height="10" fill="#222"/><path d="M1 3l7 6 7-6" fill="none" stroke="#f1f1f1" stroke-width="1.4"/></svg><p>hello@tesslyrealty.com</p></div>
    <div class="contact-row"><svg width="16" height="16" viewBox="0 0 16 16"><path d="M8 1a5 5 0 0 0-5 5c0 4 5 9 5 9s5-5 5-9a5 5 0 0 0-5-5z" fill="#222"/><circle cx="8" cy="6" r="2" fill="#f1f1f1"/></svg><p>214 Linden Row, 2, Brooklyn, New York 11200</p></div>
  </div>
  <div class="footer-col col-links abs">
    <h4>QUICK LINKS</h4>
    <ul>
      <li><svg width="8" height="10" viewBox="0 0 8 10"><path d="M1 1l4 4-4 4" fill="none" stroke="#222" stroke-width="2"/></svg>Home</li>
      <li><svg width="8" height="10" viewBox="0 0 8 10"><path d="M1 1l4 4-4 4" fill="none" stroke="#222" stroke-width="2"/></svg>About Us</li>
      <li><svg width="8" height="10" viewBox="0 0 8 10"><path d="M1 1l4 4-4 4" fill="none" stroke="#222" stroke-width="2"/></svg>Services</li>
      <li><svg width="8" height="10" viewBox="0 0 8 10"><path d="M1 1l4 4-4 4" fill="none" stroke="#222" stroke-width="2"/></svg>Contact Us</li>
      <li><svg width="8" height="10" viewBox="0 0 8 10"><path d="M1 1l4 4-4 4" fill="none" stroke="#222" stroke-width="2"/></svg>Sign up</li>
    </ul>
  </div>
</footer>
<div class="footer-bar abs">
  <p class="copyright abs">© 2019 Tessly Realty NYC &amp; Homefield</p>
  <div class="social abs"><span></span><span></span><span></span><span></span><span></span></div>
</div>

</body>
</html>
```